Moravel Aesthetic Doctor

I require an elegant, luxurious looking business card for my aesthetic business. I am a doctor and that will set me aside from competitors. I am planning to provide home and spa based treatments to clients with high expectations. I have attached my logo.

```html
<!DOCTYPE html>
<html lang="en">
<head>
<meta charset="utf-8">
<title>Moravel Aesthetic Doctor – Business Card</title>
<link rel="stylesheet" href="https://fonts.googleapis.com/css2?family=Montserrat:wght@400;500&family=Lato:wght@400&display=swap">
<style>
  :root {
    --page-bg: #e4e4e4;
    --navy: #2e3192;
    --brand-blue: #2b8fd6;
    --sky: #7fcbea;
    --pale-sky: #b6e1f3;
    --deep-wave: #2a6fbf;
    --ink: #3a3a3a;
    --white: #ffffff;
  }
  * { box-sizing: border-box; margin: 0; padding: 0; }
  html, body { width: 1200px; height: 896px; overflow: hidden; }
  body {
    background: var(--page-bg);
    position: relative;
    font-family: "Montserrat", Arial, sans-serif;
    color: var(--ink);
  }
  .card {
    position: absolute;
    left: 302px;
    width: 620px;
    height: 354px;
    overflow: hidden;
  }
  /* Front */
  .card--front { top: 95px; background: var(--navy); }
  .front-artwork {
    position: absolute;
    left: 0; top: 32px;
    width: 339px; height: 306px;
    border-radius: 0 48% 40% 0 / 0 45% 55% 0;
    background: linear-gradient(100deg, var(--deep-wave) 0%, var(--sky) 55%, var(--pale-sky) 100%);
    opacity: 0.9;
  }
  .front-wordmark {
    position: absolute;
    right: 37px; top: 256px;
    text-align: right;
    color: var(--sky);
    font-weight: 400;
    letter-spacing: 0.08em;
    line-height: 1.15;
  }
  .front-wordmark .name { display: block; font-size: 40px; }
  .front-wordmark .tag { display: block; font-size: 17px; }

  /* Back */
  .card--back { top: 469px; background: var(--white); }
  .back-logo {
    position: absolute;
    left: 56px; top: 143px;
    display: flex; align-items: center; gap: 10px;
  }
  .back-logo .mark {
    width: 64px; height: 64px; border-radius: 50%;
    background: radial-gradient(circle at 40% 45%, var(--pale-sky), var(--brand-blue));
  }
  .back-logo .wordmark {
    color: var(--brand-blue);
    font-weight: 400;
    letter-spacing: 0.06em;
    line-height: 1.1;
  }
  .back-logo .wordmark .name { display: block; font-size: 27px; }
  .back-logo .wordmark .tag { display: block; font-size: 12px; }
  .divider {
    position: absolute;
    left: 319px; top: 92px;
    width: 1px; height: 172px;
    background: var(--brand-blue);
  }
  .details {
    position: absolute;
    left: 337px; top: 88px;
    font-size: 14px;
    line-height: 1.3;
  }
  .details .doctor { color: var(--brand-blue); font-size: 17px; font-weight: 500; }
  .details .doctor small { color: var(--ink); font-size: 9px; font-weight: 400; margin-left: 3px; }
  .details .credential { margin-top: 3px; }
  .details .service-mode { margin-top: 12px; }
  .contact { list-style: none; margin-top: 14px; line-height: 1.3; }
  .contact li { display: flex; align-items: center; gap: 8px; }
  .contact svg { width: 11px; height: 11px; fill: var(--brand-blue); flex: none; }
  .social { display: inline-flex; gap: 8px; margin-left: 20px; }
  .social span { width: 10px; height: 10px; border-radius: 50%; background: var(--brand-blue); }
  .services {
    position: absolute;
    left: 0; right: 0; top: 310px;
    text-align: center;
    font-family: "Lato", Arial, sans-serif;
    font-size: 14px;
    color: var(--brand-blue);
  }
</style>
</head>
<body>
  <section class="card card--front">
    <div class="front-artwork" role="img" aria-label="Logo artwork: flowing blue waves forming a head profile"></div>
    <div class="front-wordmark">
      <span class="name">MORAVEL</span>
      <span class="tag">AESTHETIC DOCTOR</span>
    </div>
  </section>

  <section class="card card--back">
    <div class="back-logo">
      <div class="mark"></div>
      <div class="wordmark">
        <span class="name">MORAVEL</span>
        <span class="tag">AESTHETIC DOCTOR</span>
      </div>
    </div>
    <div class="divider"></div>
    <div class="details">
      <p class="doctor">Dr Elena Vasser<small>MRCPCH MD</small></p>
      <p class="credential">Australasian Diploma<br>of Aesthetic Medicine</p>
      <p class="service-mode">Home and Spa<br>Based Treatments</p>
      <ul class="contact">
        <li><svg viewBox="0 0 24 24"><path d="M6.6 10.8a15.5 15.5 0 0 0 6.6 6.6l2.2-2.2c.3-.3.7-.4 1-.2 1.1.4 2.3.6 3.6.6.6 0 1 .4 1 1V20c0 .6-.4 1-1 1C10.6 21 3 13.4 3 4c0-.6.4-1 1-1h3.5c.6 0 1 .4 1 1 0 1.3.2 2.5.6 3.6.1.3 0 .7-.2 1z"/></svg>0800 555 019</li>
        <li><svg viewBox="0 0 24 24"><path d="M2 5h20v14H2z M2 5l10 8 10-8" fill="none" stroke="#2b8fd6" stroke-width="2.4"/></svg>elena@moravel.co.nz</li>
        <li><svg viewBox="0 0 24 24"><circle cx="12" cy="12" r="9.5" fill="none" stroke="#2b8fd6" stroke-width="2"/><path d="M2.5 12h19M12 2.5c3 3 3 16 0 19M12 2.5c-3 3-3 16 0 19" fill="none" stroke="#2b8fd6" stroke-width="1.6"/></svg>www.moravel.co.nz<span class="social"><span></span><span></span></span></li>
      </ul>
    </div>
    <p class="services">Dermal injectables - Plasma facials - Microneedling Skin boosters - Excessive sweating</p>
  </section>
</body>
</html>
```